32 x 24 Swinging Real Estate Yard Sign

We are looking to design a new sign for our business to focus on the remodeling of homes to sell. We are looking to have a yard sign that gets peoples attention and is informational. The headline will be "The Secret to Top Dollar? Remodel First.". We remodel homes for sellers with no up front cost, as they simply pay at closing. This link has more info, https://bramblecresthomes.com/Remodel
The message we want to convey to those seeing the sign is we are a one stop shop, who can renovate your home and sell it for no stress. We are licensed real estate agents and licensed contractors.
Both of these license numbers and info need to be on the design:
CADRE #02794613
Contractors License #1178524
Email: info@bramblecresthomes.com
Phone: (408)614-2907
I'll attach a sample sign we have for our agents normally as well as all brand art work.
• Pantone Colors
o #172A41
Dark blue
o #4381B1
Medium blue
o #6FA6CC
Light blue
Target Market(s)
Residential Real Estate Sellers
Industry/Entity Type
Real Estate
Colors
Designer to choose colors to be used in the design.

```html
<!DOCTYPE html>
<html lang="en">
<head>
<meta charset="utf-8">
<title>Bramblecrest Homes – Remodel First Yard Sign</title>
<link href="https://fonts.googleapis.com/css2?family=League+Spartan:wght@700;800&family=Poppins:wght@400;600;700&display=swap" rel="stylesheet">
<style>
  :root {
    --navy: #172A41;
    --sky: #5AADEE;
    --steel: #4381B1;
    --white: #FFFFFF;
    --paper: #FFFFFF;
  }
  * { margin: 0; padding: 0; box-sizing: border-box; }
  html, body {
    width: 938px; height: 1200px; overflow: hidden;
    background: var(--paper);
  }
  .sign {
    position: absolute; left: 84px; top: 87px;
    width: 770px; height: 1025px;
    background: var(--navy);
    overflow: hidden;
  }
  .sign > * { position: absolute; left: 0; width: 100%; text-align: center; white-space: nowrap; }

  .brand-header { top: 0; height: 188px; background: var(--white); }
  .brand {
    position: absolute; left: 0; width: 100%; top: 44px;
    display: flex; flex-direction: column; align-items: center;
    font-family: "League Spartan", sans-serif; font-weight: 700; color: var(--navy);
  }
  .brand-name { font-size: 62px; line-height: 62px; letter-spacing: 1px; display: flex; align-items: center; gap: 16px; }
  .brand-dot { width: 34px; height: 34px; border-radius: 50%; background: var(--steel); margin-top: -8px; }
  .brand-sub { font-size: 22px; line-height: 22px; letter-spacing: 11px; margin-top: 16px; padding-left: 11px; }

  .headline-lead {
    font-family: "League Spartan", sans-serif; font-weight: 800;
    color: var(--white); font-size: 58px; line-height: 60px; letter-spacing: 0.5px;
  }
  .lead-1 { top: 229px; }
  .lead-2 { top: 289px; }
  .headline-main {
    font-family: "League Spartan", sans-serif; font-weight: 800;
    color: var(--sky); font-size: 108px; line-height: 94px; letter-spacing: 0;
  }
  .main-1 { top: 365px; }
  .main-2 { top: 459px; }

  .license-band { top: 584px; height: 144px; background: var(--sky); }
  .license {
    font-family: "Poppins", sans-serif; font-weight: 700; color: var(--navy);
    font-size: 29px; line-height: 34px; letter-spacing: 0.3px;
  }
  .license-1 { top: 614px; }
  .license-2 { top: 664px; }

  .phone {
    top: 745px; font-family: "Poppins", sans-serif; font-weight: 700;
    color: var(--white); font-size: 86px; line-height: 98px; letter-spacing: -1px;
  }
  .email {
    top: 847px; height: 46px;
    display: flex; justify-content: center; align-items: center; gap: 14px;
    font-family: "Poppins", sans-serif; font-weight: 600;
    color: var(--white); font-size: 35px; line-height: 46px;
    padding-left: 18px;
  }
  .email-icon { width: 50px; height: 50px; flex: none; }
  .web {
    top: 924px; font-family: "Poppins", sans-serif; font-weight: 400;
    color: var(--white); font-size: 37px; line-height: 46px;
  }
  .web strong { color: var(--sky); font-weight: 600; }
</style>
</head>
<body>
  <main class="sign">
    <header class="brand-header">
      <div class="brand">
        <div class="brand-name"><span class="brand-dot"></span>BRAMBLECREST</div>
        <div class="brand-sub">HOMES</div>
      </div>
    </header>

    <h1 class="headline-lead lead-1">THE SECRET TO</h1>
    <div class="headline-lead lead-2">TOP DOLLAR?</div>
    <div class="headline-main main-1">REMODEL</div>
    <div class="headline-main main-2">FIRST</div>

    <section class="license-band" aria-label="Licenses"></section>
    <p class="license license-1">CONTRACTORS LICENSE #1178524</p>
    <p class="license license-2">CADRE #02794613</p>

    <p class="phone">(408)614-2907</p>
    <p class="email">
      <svg class="email-icon" viewBox="0 0 50 50" aria-hidden="true">
        <circle cx="25" cy="25" r="25" fill="#5AADEE"/>
        <rect x="12" y="16" width="26" height="18" fill="none" stroke="#172A41" stroke-width="2.4"/>
        <path d="M12 16 L25 27 L38 16 M12 34 L21 24 M38 34 L29 24" fill="none" stroke="#172A41" stroke-width="2.2"/>
      </svg>
      info@bramblecresthomes.com
    </p>
    <p class="web">www.<strong>bramblecresthomes</strong>.com</p>
  </main>
</body>
</html>
```